Mindfulness School for Children -- Business Cards

We're looking for business cards for our school directors and owners. We're a mindfulness school for children called little lanterns. Attached are our logos/icons.

```html
<!DOCTYPE html>
<html lang="en">
<head>
<meta charset="utf-8">
<title>little lanterns — business cards</title>
<link href="https://fonts.googleapis.com/css2?family=Montserrat:wght@500;600&family=Arimo:wght@400&display=swap" rel="stylesheet">
<style>
  :root {
    --bg: #e9ecec;
    --teal-blue: #4aa8c2;
    --teal-green: #56a396;
    --mint: #8ecb9c;
    --deep-green: #4f9a88;
    --ink: #3c3c3c;
    --white: #ffffff;
  }
  * { box-sizing: border-box; margin: 0; padding: 0; }
  html, body { width: 1200px; height: 900px; overflow: hidden; }
  body {
    background: var(--bg);
    font-family: "Arimo", Arial, sans-serif;
    position: relative;
  }
  .card {
    position: absolute;
    left: 300px;
    width: 600px;
    height: 343px;
    overflow: hidden;
    box-shadow: 0 10px 24px rgba(0,0,0,0.18);
  }
  /* Back of card */
  .card-back {
    top: 80px;
    background: linear-gradient(155deg, var(--teal-green) 0%, var(--teal-blue) 45%, var(--teal-blue) 60%, var(--teal-green) 100%);
    display: flex;
    align-items: center;
    justify-content: center;
  }
  .brand {
    display: flex;
    align-items: center;
    gap: 14px;
    font-family: "Montserrat", sans-serif;
    font-weight: 500;
  }
  .brand-dot { width: 22px; height: 22px; border-radius: 50%; }
  .card-back .brand { color: var(--white); font-size: 50px; letter-spacing: 0.5px; }
  .card-back .brand-dot { background: var(--white); }

  /* Front of card */
  .card-front { top: 477px; background: var(--white); }
  .footer-band {
    position: absolute;
    left: 0; right: 0; bottom: 0;
    height: 64px;
    background: linear-gradient(90deg, var(--deep-green) 0%, var(--mint) 100%);
  }
  .person { position: absolute; left: 40px; top: 42px; }
  .person-name {
    font-family: "Montserrat", sans-serif;
    font-weight: 600;
    font-size: 30px;
    line-height: 1;
  }
  .person-name .first { color: var(--mint); }
  .person-name .last { color: var(--teal-blue); }
  .person-role { font-size: 15px; color: var(--ink); margin-top: 4px; }
  .card-front .brand {
    position: absolute; right: 36px; top: 70px;
    color: var(--teal-green); font-size: 28px; gap: 10px;
  }
  .card-front .brand-dot { background: var(--teal-green); width: 14px; height: 14px; }
  .contact {
    position: absolute; left: 52px; top: 150px;
    list-style: none; font-size: 15px; color: var(--ink); line-height: 1.45;
  }
  .contact li { display: flex; align-items: center; gap: 8px; }
  .contact svg { width: 16px; height: 16px; flex: none; }
  .contact .address { margin-top: 14px; padding-left: 24px; display: block; }
  .website {
    position: absolute; right: 30px; bottom: 24px;
    color: var(--white); font-size: 14px; letter-spacing: 0.3px;
  }
</style>
</head>
<body>

  <section class="card card-back" aria-label="Business card back">
    <div class="brand"><span class="brand-dot"></span><span>little lanterns</span></div>
  </section>

  <section class="card card-front" aria-label="Business card front">
    <div class="footer-band" aria-hidden="true"></div>

    <div class="person">
      <p class="person-name"><span class="first">Daniel</span> <span class="last">Hart</span></p>
      <p class="person-role">Managing Director</p>
    </div>

    <div class="brand"><span class="brand-dot"></span><span>little lanterns</span></div>

    <ul class="contact">
      <li>
        <svg viewBox="0 0 24 24" aria-hidden="true"><path fill="#4aa8c2" d="M6.6 10.8a15 15 0 0 0 6.6 6.6l2.2-2.2a1 1 0 0 1 1-.25 11.4 11.4 0 0 0 3.6.57 1 1 0 0 1 1 1V20a1 1 0 0 1-1 1A17 17 0 0 1 3 4a1 1 0 0 1 1-1h3.5a1 1 0 0 1 1 1c0 1.25.2 2.45.57 3.6a1 1 0 0 1-.25 1z"/></svg>
        044-555 010 246
      </li>
      <li>
        <svg viewBox="0 0 24 24" aria-hidden="true"><rect x="2" y="5" width="20" height="14" fill="#4aa8c2"/><path d="M2 5l10 8 10-8" fill="none" stroke="#fff" stroke-width="1.6"/></svg>
        hello@littlelanterns.org
      </li>
      <li class="address">18, Willow Lane Park<br>30417, Eastmoor</li>
    </ul>

    <p class="website">www.littlelanterns.org</p>
  </section>

</body>
</html>
```